Slide Master for Holloway Engines - A Systematic Hedge Fund

We are looking for someone to produce a theme and slide master for us for our investor presentations. I have uploaded a few examples of templates that we would like to have included:
Main Title
Section Title
Slides with just bullet points
Different image/table configurations with bullet points and foot notes
Biographies of different lengths
A disclaimer (no one will read this but it should still look nice and needs to be in the presentations)
I have also uploaded the company logo, business card and colour definitions. Currently we have a blue colour scheme defined, but it would be nice to get a complementary set of colours so that when we have charts with more elements we can just draw from those.
The most important thing is that the slide master must be of general use to us. We arn't looking to have a specific presentation designed for us, but a theme/style that we can apply ourselves to any presentation we need to give in the future. It should have clearly defined guidelines for where content should go (and if this is different with and without footnotes for example). We would also like it to have a similar feel to the logo/business cards, so matt colours, high contrast, but not busy.
I'm excited to see the results!

```html
<!DOCTYPE html>
<html lang="en">
<head>
<meta charset="utf-8">
<title>Holloway Engines — Slide Master</title>
<link href="https://fonts.googleapis.com/css2?family=Roboto:wght@400;500;700;900&display=swap" rel="stylesheet">
<style>
:root{
  --page:#f3f4f6;
  --navy:#17396a;
  --navy-deep:#123260;
  --title-blue:#1c3b6d;
  --accent:#4a86d8;
  --royal:#2450b0;
  --sky:#3f80d6;
  --ink:#444a55;
  --muted:#7a808a;
  --white:#ffffff;
}
*{box-sizing:border-box;margin:0;padding:0}
html,body{width:1200px;height:4175px;overflow:hidden}
body{background:var(--page);font-family:"Roboto",Arial,sans-serif;position:relative;color:var(--ink)}
.slide{position:absolute;left:37px;width:1126px;height:633px;overflow:hidden;box-shadow:0 4px 14px rgba(0,0,0,.18);background:var(--white)}
.slide--dark{background:linear-gradient(160deg,#1f4677 0%,var(--navy) 55%,var(--navy-deep) 100%);color:var(--white)}
.slide--navy{background:linear-gradient(160deg,#17386a 0%,#12305f 100%);color:var(--white)}
.brand-mark{position:absolute;top:30px;right:28px;width:106px;text-align:center;font-weight:700;font-size:14px;line-height:15px;letter-spacing:1px;color:var(--title-blue)}
.slide--dark .brand-mark,.slide--navy .brand-mark{color:var(--white)}
.brand-mark span{display:block;font-size:14px;letter-spacing:3px}
.slide-title{position:absolute;left:96px;top:56px;font-size:28px;font-weight:500;color:var(--title-blue)}
.slide--dark .slide-title,.slide--navy .slide-title{color:var(--white)}
.slide-lead{position:absolute;left:96px;top:104px;width:720px;font-size:16px;line-height:31px;color:var(--ink)}
.slide--dark .slide-lead,.slide--navy .slide-lead{color:var(--white);font-weight:500}
.base-bar{position:absolute;bottom:0;height:6px}
.base-bar--left{left:0;width:750px;background:var(--navy)}
.base-bar--right{left:753px;right:0;background:var(--accent)}
.footnote{position:absolute;left:74px;top:593px;display:flex;gap:14px;align-items:center;width:1010px}
.footnote b{font-size:10px;font-weight:500;letter-spacing:.3px}
.footnote p{font-size:7.6px;line-height:11px;color:var(--muted)}
.slide--dark .footnote p,.slide--navy .footnote p{color:#d8e2f2}

.cover{top:39px;background:linear-gradient(135deg,#1e44a4 0%,#2458c2 45%,#3e7fd6 100%)}
.cover-glow{position:absolute;inset:0;background:radial-gradient(circle at 78% 92%,rgba(214,120,210,.55) 0,rgba(150,110,220,.25) 22%,transparent 45%),radial-gradient(circle at 95% 20%,rgba(120,180,240,.35) 0,transparent 40%)}
.cover-brand{position:absolute;top:235px;left:0;right:0;text-align:center;color:var(--white);font-weight:700;font-size:70px;line-height:84px;letter-spacing:4px}
.cover-brand span{display:block;letter-spacing:26px}
.cover-tagline{position:absolute;top:448px;left:0;right:0;text-align:center;color:var(--white);font-size:27px;line-height:44px;font-weight:500}

.legal-card{position:absolute;top:152px;width:428px;height:400px;background:var(--white);box-shadow:0 3px 16px rgba(0,0,0,.16);padding:26px 16px 0 16px}
.legal-card::after{content:"";position:absolute;left:0;right:0;bottom:0;height:6px;background:var(--navy)}
.legal-card--right::after{background:var(--accent)}
.legal-card p{font-size:8.4px;line-height:14.2px;color:var(--muted);margin-bottom:14px}

.point-card{position:absolute;top:183px;width:483px;height:366px;background:var(--white);padding:38px 30px 0 30px;color:var(--ink)}
.point-card h3{font-size:22px;font-weight:500;color:var(--title-blue);margin-bottom:14px}
.point-card li{list-style:none;position:relative;padding-left:32px;font-size:10.4px;line-height:18px;height:50px}
.point-card li::before{content:"";position:absolute;left:0;top:2px;width:11px;height:11px;border:1.4px solid var(--muted);border-radius:50%}

.chart{position:absolute;top:210px}
.chart text{font-family:"Roboto",Arial,sans-serif;font-size:8px;fill:#777}
.line-chart text{fill:#d8e2f2}
.side-copy{position:absolute;left:96px;width:320px}
.side-copy h4{font-size:19px;font-weight:500;margin-bottom:10px}
.side-copy p{font-size:10.4px;line-height:21px}

.backdrop{position:absolute;left:110px;top:0;width:760px;height:330px;background:linear-gradient(180deg,#e9ecf1 0%,rgba(255,255,255,0) 100%);opacity:.8}
.bio-photo{position:absolute;top:233px;width:195px;height:194px;background:linear-gradient(160deg,#c9cfd6 0%,#6d7a88 60%,#3b4550 100%);border-top:3px solid #222}
.bio{position:absolute;top:230px;width:280px}
.bio h5{font-size:14px;font-weight:500;color:var(--title-blue)}
.bio .role{font-size:10px;color:var(--muted);margin:4px 0 6px}
.bio p{font-size:10px;line-height:16.6px;color:var(--ink)}
</style>
</head>
<body>

<section class="slide cover">
  <div class="cover-glow" role="img" aria-label="Soft connected network background in blue and violet tones"></div>
  <div class="cover-brand">HOLLOWAY<span>ENGINES</span></div>
  <p class="cover-tagline">Neque porro quisquam est qui dolorem ipsum quia dolor<br>sit amet, consectetur, adipisci velit...</p>
</section>

<section class="slide" style="top:715px">
  <h2 class="slide-title" style="left:100px;top:54px">Disclaimer</h2>
  <div class="brand-mark">HOLLOWAY<span>ENGINES</span></div>
  <div class="legal-card" style="left:100px">
    <p>Lorem ipsum dolor sit amet, consectetur adipiscing elit. Vestibulum lacinia eros eu pharetra mollis. Nullam vulputate purus mi, sed maximus est sodales mollis. Mauris nec vulputate eros. Cras lectus lacus, lacinia eu dapibus ac, tincidunt eu nisi. Suspendisse in volutpat risus. Nunc pharetra porttitor lorem. Vivamus at lectus sit amet lacus dictum tincidunt at vel magna. Donec blandit nulla ac erat condimentum, fringilla feugiat ex porttitor. Aenean facilisis pharetra lacus sed tempus.</p>
    <p>Lorem ipsum dolor sit amet, consectetur adipiscing elit. Vestibulum lacinia eros eu pharetra mollis. Nullam vulputate purus mi, sed maximus est sodales mollis. Mauris nec vulputate eros. Cras lectus lacus, lacinia eu dapibus ac, tincidunt eu nisi. Suspendisse in volutpat risus. Nunc pharetra porttitor lorem. Vivamus at lectus sit amet lacus dictum tincidunt at vel magna. Donec blandit nulla ac erat condimentum, fringilla feugiat ex porttitor. Aenean facilisis pharetra lacus sed tempus.</p>
    <p>Lorem ipsum dolor sit amet, consectetur adipiscing elit. Vestibulum lacinia eros eu pharetra mollis. Nullam vulputate purus mi, sed maximus est sodales mollis. Mauris nec vulputate eros. Cras lectus lacus, lacinia eu dapibus ac, tincidunt eu nisi. Suspendisse in volutpat risus. Nunc pharetra porttitor lorem. Vivamus at lectus sit amet lacus dictum tincidunt at vel magna. Donec blandit nulla ac erat condimentum, fringilla feugiat ex porttitor. Aenean facilisis pharetra lacus sed tempus.</p>
    <p>Lorem ipsum dolor sit amet, consectetur adipiscing elit. Vestibulum lacinia eros eu pharetra mollis. Nullam vulputate purus mi, sed maximus est sodales mollis. Mauris nec vulputate eros. Cras lectus lacus, lacinia eu dapibus ac, tincidunt eu nisi.</p>
  </div>
  <div class="legal-card legal-card--right" style="left:597px">
    <p>Lorem ipsum dolor sit amet, consectetur adipiscing elit. Vestibulum lacinia eros eu pharetra mollis. Nullam vulputate purus mi, sed maximus est sodales mollis. Mauris nec vulputate eros. Cras lectus lacus, lacinia eu dapibus ac, tincidunt eu nisi. Suspendisse in volutpat risus. Nunc pharetra porttitor lorem. Vivamus at lectus sit amet lacus dictum tincidunt at vel magna. Donec blandit nulla ac erat condimentum, fringilla feugiat ex porttitor. Aenean facilisis pharetra lacus sed tempus.</p>
    <p>Lorem ipsum dolor sit amet, consectetur adipiscing elit. Vestibulum lacinia eros eu pharetra mollis. Nullam vulputate purus mi, sed maximus est sodales mollis. Mauris nec vulputate eros. Cras lectus lacus, lacinia eu dapibus ac, tincidunt eu nisi. Suspendisse in volutpat risus. Nunc pharetra porttitor lorem. Vivamus at lectus sit amet lacus dictum tincidunt at vel magna. Donec blandit nulla ac erat condimentum, fringilla feugiat ex porttitor. Aenean facilisis pharetra lacus sed tempus.</p>
    <p>Lorem ipsum dolor sit amet, consectetur adipiscing elit. Vestibulum lacinia eros eu pharetra mollis. Nullam vulputate purus mi, sed maximus est sodales mollis. Mauris nec vulputate eros. Cras lectus lacus, lacinia eu dapibus ac, tincidunt eu nisi. Suspendisse in volutpat risus. Nunc pharetra porttitor lorem. Vivamus at lectus sit amet lacus dictum tincidunt at vel magna. Donec blandit nulla ac erat condimentum, fringilla feugiat ex porttitor. Aenean facilisis pharetra lacus sed tempus.</p>
    <p>Lorem ipsum dolor sit amet, consectetur adipiscing elit. Vestibulum lacinia eros eu pharetra mollis. Nullam vulputate purus mi, sed maximus est sodales mollis. Mauris nec vulputate eros. Cras lectus lacus, lacinia eu dapibus ac, tincidunt eu nisi.</p>
  </div>
  <div class="base-bar base-bar--left"></div>
  <div class="base-bar base-bar--right"></div>
</section>

<section class="slide slide--dark" style="top:1391px">
  <h2 class="slide-title">Neque porro quisquam est qui dolorem ipsum</h2>
  <p class="slide-lead">Lorem Ipsum is simply dummy text of the printing and typesetting industry. Lorem Ipsum has been the industry's standard dummy text ever since the 1500s,</p>
  <div class="brand-mark">HOLLOWAY<span>ENGINES</span></div>
  <div class="point-card" style="left:60px">
    <h3>Neque porro quisquam est qui dolorem</h3>
    <ul>
      <li>It is a long established fact that a reader will be distracted by the readable content of a page when looking at its layout.</li>
      <li>It is a long established fact that a reader will be distracted by the readable content of a page when looking at its layout.</li>
      <li>It is a long established fact that a reader will be distracted by the readable content of a page when looking at its layout.</li>
      <li>It is a long established fact that a reader will be distracted by the readable content of a page when looking at its layout.</li>
      <li>It is a long established fact that a reader will be distracted by the readable content of a page when looking at its layout.</li>
    </ul>
  </div>
  <div class="point-card" style="left:563px;width:529px">
    <h3>Neque porro quisquam est qui dolorem</h3>
    <ul>
      <li>It is a long established fact that a reader will be distracted by the readable content of a page when looking at its layout.</li>
      <li>It is a long established fact that a reader will be distracted by the readable content of a page when looking at its layout.</li>
      <li>It is a long established fact that a reader will be distracted by the readable content of a page when looking at its layout.</li>
      <li>It is a long established fact that a reader will be distracted by the readable content of a page when looking at its layout.</li>
      <li>It is a long established fact that a reader will be distracted by the readable content of a page when looking at its layout.</li>
    </ul>
  </div>
  <div class="footnote"><b>DISCLAIMER</b><p>It is a long established fact that a reader will be distracted by the readable content of a page when looking at its layout. The point of using Lorem Ipsum is that it has a more-or-less normal distribution of letters, as opposed to using 'Content here, content here', making it look like readable English. Many desktop publishing packages and web page editors now use Lorem Ipsum as their default model text, and a search for 'lorem ipsum'</p></div>
  <div class="base-bar base-bar--right"></div>
</section>

<section class="slide" style="top:2066px">
  <h2 class="slide-title">Neque porro quisquam est qui dolorem ipsum</h2>
  <p class="slide-lead">Lorem Ipsum is simply dummy text of the printing and typesetting industry. Lorem Ipsum has been the industry's standard dummy text ever since the 1500s,</p>
  <div class="brand-mark">HOLLOWAY<span>ENGINES</span></div>
  <svg width="0" height="0" style="position:absolute">
    <defs>
      <linearGradient id="barDark" x1="0" y1="0" x2="0" y2="1"><stop offset="0" stop-color="#1f4fa3"/><stop offset="1" stop-color="#1f4fa3" stop-opacity=".15"/></linearGradient>
      <linearGradient id="barMid" x1="0" y1="0" x2="0" y2="1"><stop offset="0" stop-color="#4f87d2"/><stop offset="1" stop-color="#4f87d2" stop-opacity=".15"/></linearGradient>
      <linearGradient id="barLight" x1="0" y1="0" x2="0" y2="1"><stop offset="0" stop-color="#b3cbee"/><stop offset="1" stop-color="#b3cbee" stop-opacity=".2"/></linearGradient>
      <symbol id="barChart" viewBox="0 0 470 310">
        <g stroke="#e3e6ea" stroke-width="1">
          <line x1="30" y1="20" x2="460" y2="20"/><line x1="30" y1="43" x2="460" y2="43"/><line x1="30" y1="66" x2="460" y2="66"/><line x1="30" y1="89" x2="460" y2="89"/><line x1="30" y1="112" x2="460" y2="112"/><line x1="30" y1="135" x2="460" y2="135"/><line x1="30" y1="158" x2="460" y2="158"/><line x1="30" y1="181" x2="460" y2="181"/><line x1="30" y1="204" x2="460" y2="204"/><line x1="30" y1="227" x2="460" y2="227"/><line x1="30" y1="250" x2="460" y2="250"/>
        </g>
        <g text-anchor="end" font-family="Roboto, Arial, sans-serif" font-size="8" fill="#777">
          <text x="22" y="23">1000</text><text x="22" y="46">900</text><text x="22" y="69">800</text><text x="22" y="92">700</text><text x="22" y="115">600</text><text x="22" y="138">500</text><text x="22" y="161">400</text><text x="22" y="184">300</text><text x="22" y="207">200</text><text x="22" y="230">100</text><text x="22" y="253">0%</text>
        </g>
        <rect x="30" y="215" width="26" height="35" fill="url(#barLight)"/>
        <rect x="50" y="176" width="26" height="74" fill="url(#barMid)"/>
        <rect x="72" y="59" width="26" height="191" fill="url(#barDark)"/>
        <rect x="92" y="218" width="26" height="32" fill="url(#barLight)"/>
        <rect x="112" y="140" width="26" height="110" fill="url(#barDark)"/>
        <rect x="132" y="167" width="26" height="83" fill="url(#barMid)"/>
        <rect x="150" y="183" width="26" height="67" fill="url(#barDark)"/>
        <rect x="170" y="165" width="26" height="85" fill="url(#barMid)"/>
        <rect x="190" y="220" width="26" height="30" fill="url(#barDark)"/>
        <rect x="210" y="190" width="26" height="60" fill="url(#barLight)"/>
        <rect x="228" y="133" width="26" height="117" fill="url(#barDark)"/>
        <rect x="248" y="199" width="26" height="51" fill="url(#barMid)"/>
        <rect x="268" y="170" width="26" height="80" fill="url(#barLight)"/>
        <rect x="288" y="197" width="26" height="53" fill="url(#barDark)"/>
        <rect x="308" y="151" width="26" height="99" fill="url(#barDark)"/>
        <rect x="328" y="117" width="26" height="133" fill="url(#barDark)"/>
        <rect x="350" y="236" width="26" height="14" fill="url(#barLight)"/>
        <rect x="372" y="183" width="26" height="67" fill="url(#barLight)"/>
        <rect x="392" y="34" width="26" height="216" fill="url(#barDark)"/>
        <g transform="translate(0,268)" font-family="Roboto, Arial, sans-serif" font-size="7" fill="#777">
          <text x="30" y="0" transform="rotate(-20 30 0)">151,167</text><text x="58" y="0" transform="rotate(-20 58 0)">151,167</text><text x="86" y="0" transform="rotate(-20 86 0)">151,167</text><text x="114" y="0" transform="rotate(-20 114 0)">151,167</text><text x="142" y="0" transform="rotate(-20 142 0)">151,167</text><text x="170" y="0" transform="rotate(-20 170 0)">151,167</text><text x="198" y="0" transform="rotate(-20 198 0)">151,167</text><text x="226" y="0" transform="rotate(-20 226 0)">151,167</text><text x="254" y="0" transform="rotate(-20 254 0)">151,167</text><text x="282" y="0" transform="rotate(-20 282 0)">151,167</text><text x="310" y="0" transform="rotate(-20 310 0)">151,167</text><text x="338" y="0" transform="rotate(-20 338 0)">151,167</text><text x="366" y="0" transform="rotate(-20 366 0)">151,167</text><text x="394" y="0" transform="rotate(-20 394 0)">151,167</text><text x="422" y="0" transform="rotate(-20 422 0)">151,167</text>
        </g>
      </symbol>
    </defs>
  </svg>
  <svg class="chart" style="left:58px" width="470" height="310" viewBox="0 0 470 310"><use href="#barChart" x="0" y="0" width="470" height="310"/></svg>
  <svg class="chart" style="left:572px" width="470" height="310" viewBox="0 0 470 310"><use href="#barChart" x="0" y="0" width="470" height="310"/></svg>
  <div class="footnote"><b>DISCLAIMER</b><p>It is a long established fact that a reader will be distracted by the readable content of a page when looking at its layout. The point of using Lorem Ipsum is that it has a more-or-less normal distribution of letters, as opposed to using 'Content here, content here', making it look like readable English. Many desktop publishing packages and web page editors now use Lorem Ipsum as their default model text, and a search for 'lorem ipsum'</p></div>
  <div class="base-bar base-bar--left"></div>
  <div class="base-bar base-bar--right"></div>
</section>

<section class="slide slide--navy" style="top:2744px">
  <h2 class="slide-title">Neque porro quisquam est qui dolorem ipsum</h2>
  <p class="slide-lead">Lorem Ipsum is simply dummy text of the printing and typesetting industry. Lorem Ipsum has been the industry's standard dummy text ever since the 1500s,</p>
  <div class="brand-mark">HOLLOWAY<span>ENGINES</span></div>
  <div class="side-copy" style="top:242px"><h4>Neque porro quisquam</h4><p>Lorem Ipsum is simply dummy text of the printing and typesetting industry. Lorem Ipsum has been the industry's standard dummy text ever since the</p></div>
  <div class="side-copy" style="top:377px"><h4>Neque porro quisquam</h4><p>Lorem Ipsum is simply dummy text of the printing and typesetting industry. Lorem Ipsum has been the industry's standard dummy text ever since the</p></div>
  <svg class="chart line-chart" style="left:522px;top:222px" width="500" height="300" viewBox="0 0 500 300">
    <g stroke="#4a6a98" stroke-width="1">
      <line x1="36" y1="20" x2="490" y2="20"/><line x1="36" y1="43" x2="490" y2="43"/><line x1="36" y1="66" x2="490" y2="66"/><line x1="36" y1="89" x2="490" y2="89"/><line x1="36" y1="112" x2="490" y2="112"/><line x1="36" y1="135" x2="490" y2="135"/><line x1="36" y1="158" x2="490" y2="158"/><line x1="36" y1="181" x2="490" y2="181"/><line x1="36" y1="204" x2="490" y2="204"/><line x1="36" y1="227" x2="490" y2="227"/><line x1="36" y1="250" x2="490" y2="250"/>
    </g>
    <g text-anchor="end">
      <text x="26" y="23">1000</text><text x="26" y="46">900</text><text x="26" y="69">800</text><text x="26" y="92">700</text><text x="26" y="115">600</text><text x="26" y="138">500</text><text x="26" y="161">400</text><text x="26" y="184">300</text><text x="26" y="207">200</text><text x="26" y="230">100</text><text x="26" y="253">0%</text>
    </g>
    <g fill="none" stroke-width="3" stroke-linejoin="round" stroke-linecap="round">
      <polyline stroke="#7a2ff0" points="36,250 57,215 89,181 187,146 268,135 316,77 365,20 427,20"/>
      <polyline stroke="#3a3fe0" points="36,250 57,233 89,221 130,190 219,181 268,66 316,54 345,121 373,144 422,158 483,165"/>
      <polyline stroke="#2f6fe0" points="36,250 89,238 130,234 187,227 243,195 287,174 337,140 401,105 466,84 466,61"/>
    </g>
    <g fill="#7fa6e6" stroke="#c6d6f5" stroke-width="1.5">
      <circle cx="36" cy="250" r="6"/><circle cx="57" cy="215" r="6"/><circle cx="89" cy="181" r="6"/><circle cx="187" cy="146" r="6"/><circle cx="268" cy="135" r="6"/><circle cx="316" cy="77" r="6"/><circle cx="365" cy="20" r="6"/><circle cx="427" cy="20" r="6"/>
      <circle cx="57" cy="233" r="6"/><circle cx="89" cy="221" r="6"/><circle cx="130" cy="190" r="6"/><circle cx="219" cy="181" r="6"/><circle cx="268" cy="66" r="6"/><circle cx="316" cy="54" r="6"/><circle cx="345" cy="121" r="6"/><circle cx="373" cy="144" r="6"/><circle cx="422" cy="158" r="6"/><circle cx="483" cy="165" r="6"/>
      <circle cx="89" cy="238" r="6"/><circle cx="130" cy="234" r="6"/><circle cx="187" cy="227" r="6"/><circle cx="243" cy="195" r="6"/><circle cx="287" cy="174" r="6"/><circle cx="337" cy="140" r="6"/><circle cx="401" cy="105" r="6"/><circle cx="466" cy="84" r="6"/><circle cx="466" cy="61" r="6"/>
    </g>
    <g transform="translate(0,272)" font-size="7">
      <text x="36" y="0" transform="rotate(-20 36 0)">151,167</text><text x="66" y="0" transform="rotate(-20 66 0)">151,167</text><text x="96" y="0" transform="rotate(-20 96 0)">151,167</text><text x="126" y="0" transform="rotate(-20 126 0)">151,167</text><text x="156" y="0" transform="rotate(-20 156 0)">151,167</text><text x="186" y="0" transform="rotate(-20 186 0)">151,167</text><text x="216" y="0" transform="rotate(-20 216 0)">151,167</text><text x="246" y="0" transform="rotate(-20 246 0)">151,167</text><text x="276" y="0" transform="rotate(-20 276 0)">151,167</text><text x="306" y="0" transform="rotate(-20 306 0)">151,167</text><text x="336" y="0" transform="rotate(-20 336 0)">151,167</text><text x="366" y="0" transform="rotate(-20 366 0)">151,167</text><text x="396" y="0" transform="rotate(-20 396 0)">151,167</text><text x="426" y="0" transform="rotate(-20 426 0)">151,167</text><text x="456" y="0" transform="rotate(-20 456 0)">151,167</text>
    </g>
  </svg>
  <div class="footnote"><b>DISCLAIMER</b><p>It is a long established fact that a reader will be distracted by the readable content of a page when looking at its layout. The point of using Lorem Ipsum is that it has a more-or-less normal distribution of letters, as opposed to using 'Content here, content here', making it look like readable English. Many desktop publishing packages and web page editors now use Lorem Ipsum as their default model text, and a search for 'lorem ipsum'</p></div>
  <div class="base-bar base-bar--right"></div>
</section>

<section class="slide" style="top:3420px">
  <div class="backdrop" role="img" aria-label="Faint desk scene with laptop and office items behind the heading"></div>
  <h2 class="slide-title" style="font-weight:700">BIOGRAPHIES</h2>
  <p class="slide-lead">Lorem Ipsum is simply dummy text of the printing and typesetting industry. Lorem Ipsum has been the industry's standard dummy text ever since the 1500s,</p>
  <div class="brand-mark">HOLLOWAY<span>ENGINES</span></div>
  <div class="bio-photo" style="left:55px" role="img" aria-label="Portrait photo of Daniel R Whitaker holding a tablet"></div>
  <div class="bio" style="left:268px">
    <h5>Daniel R Whitaker</h5>
    <p class="role">Northgate</p>
    <p>Lorem ipsum dolor sit amet, consectetur adipiscing elit. Vestibulum lacinia eros eu pharetra mollis. Nullam vulputate purus mi, sed maximus est sodales mollis. Mauris nec vulputate eros. Cras lectus lacus, lacinia eu dapibus ac, tincidunt eu nisi. Suspendisse in volutpat risus. Nunc pharetra porttitor lorem. Vivamus at lectus sit amet lacus dictum tincidunt at vel magna. Donec blandit nulla ac erat condimentum, fringilla feugiat ex porttitor. Proin est odio, suscipit vitae magna at, bibendum tincidunt mi. Aenean facilisis pharetra lacus sed tempus. Nam finibus eu diam eu consectetur. Donec blandit nulla ac erat condimentum, fringilla feugiat ex porttitor.</p>
  </div>
  <div class="bio-photo" style="left:571px;width:199px" role="img" aria-label="Portrait photo of Daniel R Whitaker working at a laptop"></div>
  <div class="bio" style="left:788px">
    <h5>Daniel R Whitaker</h5>
    <p class="role">Northgate</p>
    <p>Lorem ipsum dolor sit amet, consectetur adipiscing elit. Vestibulum lacinia eros eu pharetra mollis. Nullam vulputate purus mi, sed maximus est sodales mollis. Mauris nec vulputate eros. Cras lectus lacus, lacinia eu dapibus ac, tincidunt eu nisi. Suspendisse in volutpat risus. Nunc pharetra porttitor lorem. Vivamus at lectus sit amet lacus dictum tincidunt at vel magna. Donec blandit nulla ac erat condimentum, fringilla feugiat ex porttitor. Proin est odio, suscipit vitae magna at, bibendum tincidunt mi. Aenean facilisis pharetra lacus sed tempus. Nam finibus eu diam eu consectetur. Donec blandit nulla ac erat condimentum, fringilla feugiat ex porttitor.</p>
  </div>
  <div class="footnote"><b>DISCLAIMER</b><p>It is a long established fact that a reader will be distracted by the readable content of a page when looking at its layout. The point of using Lorem Ipsum is that it has a more-or-less normal distribution of letters, as opposed to using 'Content here, content here', making it look like readable English. Many desktop publishing packages and web page editors now use Lorem Ipsum as their default model text, and a search for 'lorem ipsum'</p></div>
  <div class="base-bar base-bar--left"></div>
  <div class="base-bar base-bar--right"></div>
</section>

</body>
</html>
```